Google Form Graphic to suit our Brand and industry

Create a graphic / image for us to put at the top of our client enquiry google form.
The image will be a section of an architectural home with our branding over the top. Preferably translucent.
The image must suit the shape of the google forms image, which is an elongated rectangle
#003d5d - brand colour

Target Market(s)

residential home owners, high end architectural homes

Industry/Entity Type

Residential construction

Colors
0054AA
0677BA
7BADD7
CADEEF
E8F1F8

Requirements
Must have
• our branding and a photo of an architectural home in the background

```html
<!DOCTYPE html>
<html lang="en">
<head>
<meta charset="utf-8">
<title>Vanta Buildworks – New Client Enquiry Form</title>
<link rel="stylesheet" href="https://fonts.googleapis.com/css2?family=Inter:wght@400;500;600&family=Montserrat:wght@500&display=swap">
<style>
  :root {
    --brand-navy: #003d5d;
    --photo-light: #4a90a3;
    --photo-mid: #2f6f86;
    --photo-deep: #163f55;
    --page-bg: #f0f2f5;
    --card-bg: #ffffff;
    --card-border: #dadce0;
    --ink: #202124;
    --ink-muted: #5f6368;
    --required: #d93025;
    --link: #1a73e8;
    --wordmark: #ffffff;
  }
  html, body {
    margin: 0;
    padding: 0;
    width: 1200px;
    height: 729px;
    overflow: hidden;
    background: var(--page-bg);
    font-family: "Inter", sans-serif;
  }
  .canvas {
    position: relative;
    width: 1200px;
    height: 729px;
  }
  .form-header {
    position: absolute;
    left: 12px;
    top: 12px;
    width: 1178px;
    height: 291px;
    border-radius: 12px;
    overflow: hidden;
    background: var(--brand-navy);
  }
  .form-header svg {
    position: absolute;
    inset: 0;
    width: 100%;
    height: 100%;
    display: block;
  }
  .wordmark {
    position: absolute;
    left: 0;
    right: 0;
    top: 146px;
    transform: translateY(-50%);
    margin: 0;
    text-align: center;
    font-family: "Montserrat", sans-serif;
    font-weight: 500;
    font-size: 60px;
    letter-spacing: 0.2em;
    padding-left: 0.2em;
    line-height: 1;
    color: var(--wordmark);
  }
  .form-card {
    position: absolute;
    left: 12px;
    top: 324px;
    width: 1176px;
    height: 394px;
    background: var(--card-bg);
    border: 1px solid var(--card-border);
    border-radius: 12px;
    overflow: hidden;
    box-sizing: border-box;
  }
  .form-card::before {
    content: "";
    position: absolute;
    left: 0;
    right: 0;
    top: 0;
    height: 15px;
    background: var(--brand-navy);
  }
  .form-title {
    position: absolute;
    left: 37px;
    top: 48px;
    margin: 0;
    font-size: 48px;
    font-weight: 600;
    line-height: 1.2;
    color: var(--ink);
  }
  .form-description {
    position: absolute;
    left: 37px;
    top: 143px;
    margin: 0;
    font-size: 22px;
    font-weight: 400;
    line-height: 1.2;
    color: var(--ink);
  }
  .field-label {
    position: absolute;
    left: 37px;
    top: 206px;
    margin: 0;
    font-size: 23px;
    font-weight: 500;
    line-height: 1.2;
    color: var(--ink);
  }
  .field-label .required {
    color: var(--required);
    margin-left: 4px;
  }
  .field-input {
    position: absolute;
    left: 37px;
    top: 258px;
    width: 551px;
    height: 40px;
    border-bottom: 1px solid var(--card-border);
    font-size: 20px;
    line-height: 30px;
    color: var(--ink-muted);
  }
  .collect-note {
    position: absolute;
    left: 37px;
    top: 328px;
    margin: 0;
    font-size: 20px;
    line-height: 1.2;
    color: var(--ink-muted);
  }
  .collect-note .settings-link {
    color: var(--link);
    margin-left: 8px;
  }
</style>
</head>
<body>
  <main class="canvas">
    <header class="form-header">
      <svg viewBox="0 0 1178 291" preserveAspectRatio="none">
        <defs>
          <linearGradient id="roofPhotoTone" x1="0" y1="0" x2="1" y2="1">
            <stop offset="0" stop-color="var(--photo-light)"/>
            <stop offset="0.55" stop-color="var(--photo-mid)"/>
            <stop offset="1" stop-color="var(--photo-deep)"/>
          </linearGradient>
        </defs>
        <rect class="home-photo" x="0" y="0" width="1178" height="291" fill="url(#roofPhotoTone)" role="img" aria-label="Photo of the pitched rooflines of an architectural home under a translucent teal overlay"/>
        <path class="brand-panel" d="M0 0 H530 C470 50 440 100 445 160 C450 220 490 260 540 291 H0 Z" fill="var(--brand-navy)"/>
      </svg>
      <h1 class="wordmark">VANTA BUILDWORKS</h1>
    </header>

    <section class="form-card">
      <h2 class="form-title">New Client Enquiry Form</h2>
      <p class="form-description">We would love to hear your thoughts or feedback on how we can improve your experience!</p>
      <p class="field-label">Email<span class="required">*</span></p>
      <div class="field-input">Valid email</div>
      <p class="collect-note">This form is collecting emails.<span class="settings-link">Change settings</span></p>
    </section>
  </main>
</body>
</html>
```